Companybrochure for Consulting & Financing Firm

I need to have a Company Brochure asap for our company. We have a website that describes what we do, but we need also a brochure, that can be sent by PDF of eventually be printed as well.

The brochure should be short but nice and appealing to the customers.

We provide professional management consulting and help our customers to get finance for very diferent projects. Our business has a lot to do with personal relations, but also we are very professional in the way we work and how develop the solutions for our clients. Our clients are mainly government-owned firm, but also private trading companies and wealthy private investors.

Our customers are mainly in Latin America, but the company is headquater is in Switzerland. We are opening offices in Panama and Caracas, this should be easaly be adabtable later.

Please have a look at our website www.vorelpartners.ch. In the brochure, we would segment our services in 1.) Project Developments 2.) Management Conulting 3.) Investment Management and 4.) Finance Solutions.

Also do have a look at www.vorelpartners.ch
(Click E for the English version)
Updates

I managed to put the Mock-Up to the Website.
It is actually not really a mock-up, it is a version I have designed myself.
Well as I am not a designer, I hope you can make it much better.
The content however is what I would put in any other design as well.

Target Market(s)

Top Management, Investors, Entrepreneurs, Government Officials

Industry/Entity Type

Management Consulting

Requirements
Must have
• Design should reflect this image elements:

We are entrepreneurs.
We are comitted to get things done.
We work closely with the client side by side.
We are a professional partner.
We are not afraid of delivering unconventional solutions.
We look at the problem from various angles.
We analyse, develop solutions and implent results.
Should not have
• Typical US-American style elements. We do not want to give the impression of being a US company.

We do not want to appear to be neo-liberal. We are a politically neutral professional consulting firm.

```html
<!DOCTYPE html>
<html lang="en">
<head>
<meta charset="utf-8">
<title>Project Development &amp; Management Consulting – Brochure Spread</title>
<link rel="stylesheet" href="https://fonts.googleapis.com/css2?family=PT+Sans:wght@400;700&display=swap">
<style>
  :root {
    --brand-blue: #5b7bbf;
    --page-white: #ffffff;
    --canvas-bg: #ffffff;
    --ink: #111111;
    --fold-line: #b9b9b9;
    --photo-light: #dfe8ee;
    --photo-mid: #9fb4c4;
    --photo-deep: #5f7486;
  }
  * { box-sizing: border-box; margin: 0; padding: 0; }
  html, body {
    width: 1200px; height: 900px; overflow: hidden;
    background: var(--canvas-bg);
    font-family: "PT Sans", "Myriad Pro", Arial, sans-serif;
  }
  .spread {
    position: absolute; left: 112px; top: 105px;
    width: 976px; height: 690px;
    background: var(--page-white);
    box-shadow: 0 0 3px rgba(0,0,0,.18);
    overflow: hidden;
  }
  .header-band {
    position: absolute; left: 0; top: 0; width: 100%; height: 137px;
    background: var(--brand-blue);
  }
  .section {
    position: absolute; top: 0; width: 487px; height: 100%;
  }
  .section--left { left: 0; }
  .section--right { left: 488px; }
  .section-title {
    position: absolute; left: 46px; top: 86px;
    color: var(--page-white);
    font-weight: 700; font-size: 16.5px; line-height: 20px;
    letter-spacing: .9px; text-transform: uppercase;
  }
  .section-body {
    position: absolute; left: 46px; top: 161px; width: 252px;
    color: var(--ink); font-weight: 700; font-size: 8.4px; line-height: 12.4px;
  }
  .section-body p + p { margin-top: 12.4px; }
  .process {
    position: absolute; left: 47px; top: 251px;
    display: flex; align-items: center;
  }
  .process-step {
    width: 72px; height: 29px; background: var(--brand-blue);
    color: var(--page-white); font-weight: 700; font-size: 7.6px;
    letter-spacing: .4px; display: flex; align-items: center; justify-content: center;
  }
  .process-arrow { width: 20px; height: 14px; display: block; }
  .section-body--second { top: 307px; }
  .photo-rule {
    position: absolute; left: 0; top: 413px; width: 100%; height: 2px;
    background: var(--brand-blue);
  }
  .photo {
    position: absolute; left: 0; top: 415px; width: 100%; height: 275px;
    background:
      radial-gradient(ellipse 30% 60% at 70% 75%, rgba(110,110,115,.55), transparent 70%),
      radial-gradient(ellipse 35% 55% at 20% 55%, rgba(150,175,195,.6), transparent 70%),
      linear-gradient(180deg, var(--photo-light) 0%, var(--photo-mid) 55%, var(--photo-deep) 100%);
  }
  .fold-line {
    position: absolute; left: 599px; top: 78px; height: 745px;
    border-left: 1px dashed var(--fold-line);
  }
</style>
</head>
<body>
  <div class="spread">
    <div class="header-band"></div>

    <section class="section section--left">
      <h2 class="section-title">Project<br>Development</h2>
      <div class="section-body">
        <p>Sometimes a project with high potential has to be developed before its economic value becomes apparent.</p>
        <p>In such situations, we participate financially in the project and commit ourselves as entrepreneurs together with the owners.</p>
        <p>We also take care of project management.</p>
      </div>
    </section>

    <section class="section section--right">
      <h2 class="section-title">Management<br>Consulting</h2>
      <div class="section-body">
        <p>We elaborate solutions together with our customers and business partners by assisting owners and top management in structured decision making.</p>
        <p>We work goal-oriented following the principle:</p>
      </div>
      <div class="process">
        <div class="process-step">ANALYSIS</div>
        <svg class="process-arrow" viewBox="0 0 20 14" aria-hidden="true"><path d="M3 5h7V1l7 6-7 6V9H3z" fill="#5b7bbf"/></svg>
        <div class="process-step">SOLUTIONS</div>
        <svg class="process-arrow" viewBox="0 0 20 14" aria-hidden="true"><path d="M3 5h7V1l7 6-7 6V9H3z" fill="#5b7bbf"/></svg>
        <div class="process-step">RESULTS</div>
      </div>
      <div class="section-body section-body--second">
        <p>Our consulting team members do all have many years of experience from previous assignments at leading international management consulting companies and are familiar with methodologies used in management consulting. We complete the team of consultants with the appropriate subject matter experts.</p>
      </div>
    </section>

    <div class="photo-rule"></div>
    <div class="photo" role="img" aria-label="Photograph: two engineers in hard hats and suits looking across a blurred construction site with modern buildings"></div>
  </div>
  <div class="fold-line"></div>
</body>
</html>
```